Small legal and financial translation company needs Squarespace website, brochure and logo

Hello,
We are Lumarin Services (www.lumarinservices-example.com), a boutique legal and financial translation company. We offer our services mainly to Spanish customers. Our primary line of business is the translation of financial statements, but we translate a wide variety legal and financial texts.
The project we are offering comprises three parts: a redo of the current website, an informational brochure for potential customer and a logo design. These three parts should provide a consistent image. We would develop content soon.
We are looking for a website that would look like a typical law firm website, nothing too fancy. Right now, it is in English, Spanish and French, although the new site need only be in English and Spanish. There must be good toggling between the English and Spanish versions. There would be no need for tie-ins to social media and it would not contain a blog. Basically, a static site. We aren't interesting in driving traffic to the site or SEO, as we will contact nearly all potential customers beforehand. The website must be built in Squarespace to enable a smooth transition. The content would be similar to the current page, we'll be working on the exact content, but a rough draft is attached.
The brochure will be some three pages and would introduce the company to potential customers, using similar images as the website and the logo to be designed.
The only specifications for the logo is, as the website and brochure, it convey a sense of security and trust.
Feel free to ask with any questions as this is the first time we have used this platform.
Thank you!
Updates

I've added a more or less final version for the text in the brochure and updated the brief. Added Wednesday, June 10, 2015

Target Market(s)

Spanish law firms, auditors, accountants, banks, investment firms

Industry/Entity Type

Finance

Logo Text

Lumarin Services

Number of Pages Required

5+ page

Font styles to use
Serif

Requirements
Must have
• The website must be built in Squarespace and have a good option to toggle between English and Spanish versions.
• Brochure must be in both English and Spanish, I'm attaching a rough draft of the information that it will probably have. This should give an idea about what to include and the spacing. I will update it to include the final information.
Nice to have
• Would be nice to have some quality finance- and legal-related images
Should not have
• Vibrant colours

```html
<!DOCTYPE html>
<html lang="en">
<head>
<meta charset="utf-8">
<title>Lumarin Services Brochure</title>
<link rel="stylesheet" href="https://fonts.googleapis.com/css2?family=EB+Garamond:wght@400;500;700&family=Oswald:wght@600&display=swap">
<style>
:root{
  --ink:#111;
  --black:#0c0c0c;
  --white:#fff;
  --stage:#ececec;
  --grey:#d9d9d9;
  --rowline:#c4c4c4;
  --text:#2a2a2a;
  --lighttext:#e8e8e8;
}
*{margin:0;padding:0;box-sizing:border-box}
html,body{width:713px;height:1200px;overflow:hidden;background:var(--stage)}
body{position:relative;font-family:"EB Garamond",Georgia,serif;color:var(--text)}
.section-label{position:absolute;left:0;width:713px;text-align:center;font-family:"Oswald",Arial,sans-serif;font-weight:600;font-size:15px;color:var(--ink);letter-spacing:.2px}
.sheet{position:absolute;left:27px;width:654px;height:504px;background:var(--white);overflow:hidden}
.sheet-outside{top:88px}
.sheet-inside{top:667px;height:505px}
.panel{position:absolute;top:0;height:100%}
.p1{left:0;width:220px}
.p2{left:220px;width:215px;background:var(--black);color:var(--lighttext)}
.p3{left:435px;width:219px}
.abs{position:absolute}
.photo{position:absolute}
.layer{position:absolute;z-index:2}
h2.serif-head{font-weight:400;font-size:13px;color:var(--ink)}
.body-copy{font-size:7.3px;line-height:9.6px;text-align:justify;color:var(--text)}
.why-title{position:absolute;top:26px;width:100%;text-align:center;font-size:16px;color:var(--white)}
.benefit{position:absolute;width:100%;text-align:center;font-size:7.5px;line-height:10px;color:var(--lighttext)}
.benefit svg{display:block;margin:0 auto 4px}
.contact{position:absolute;width:100%;text-align:center;font-size:7.5px;line-height:19px;color:var(--lighttext)}
.brand{position:absolute;z-index:2;top:26px;left:0;width:219px;text-align:center;font-size:19px;line-height:24px;letter-spacing:1px;color:var(--ink);white-space:nowrap}
.tagline{position:absolute;z-index:2;top:352px;width:100%;text-align:center;font-size:13.5px;line-height:20px;color:var(--white)}
.weburl{position:absolute;z-index:2;top:465px;width:100%;text-align:center;font-size:10.5px;color:var(--white)}
.expertise-title{position:absolute;left:11px;top:19px;font-size:15px;color:var(--ink)}
.expertise-item{position:absolute;left:11px;width:200px}
.expertise-item .num{position:absolute;left:0;top:0;width:25px;height:25px;border:1px solid var(--ink);border-radius:50%;text-align:center;font-size:14px;line-height:23px;color:var(--ink)}
.expertise-item h3{position:absolute;left:39px;top:-2px;font-size:8.5px;font-weight:700;color:var(--ink)}
.expertise-item p{position:absolute;left:39px;top:10px;width:166px}
.diff-title{position:absolute;left:14px;top:16px;width:178px;font-size:14px;line-height:20px;color:var(--white)}
.dark-copy{position:absolute;left:14px;width:190px;font-size:6.9px;line-height:8.6px;text-align:justify;color:var(--lighttext)}
.bullets{position:absolute;left:14px;top:157px;list-style:none;font-size:6.9px;color:var(--lighttext)}
.bullets li{height:21.3px}
.bullets li::before{content:"• "}
.pricing-title{position:absolute;left:10px;top:170px;font-size:16px;color:var(--ink)}
.price-table{position:absolute;left:8px;top:199px;width:201px;border-collapse:collapse;font-size:7px}
.price-table th{background:var(--black);color:var(--white);font-weight:700;font-size:8px;height:32px;text-align:left;padding-left:10px}
.price-table th.amt{text-align:center;padding-left:0}
.price-table td{background:var(--grey);height:25.8px;border-bottom:1px solid var(--rowline);padding-left:10px;color:var(--text)}
.price-table td.amt{text-align:center;padding-left:0;border-left:2px solid var(--white)}
</style>
</head>
<body>

<div class="section-label" style="top:38px">BROCHURE OUTSIDE</div>

<div class="sheet sheet-outside">
  <div class="panel p1">
    <svg class="photo" width="220" height="180" viewBox="0 0 220 180" role="img" aria-label="Photo of a group of business professionals in suits">
      <defs><linearGradient id="g1" x1="0" y1="0" x2="1" y2="1"><stop offset="0" stop-color="#d4d4d4"/><stop offset=".5" stop-color="#8a8a8a"/><stop offset="1" stop-color="#3c3c3c"/></linearGradient></defs>
      <polygon points="0,0 220,0 220,166 0,112" fill="url(#g1)"/>
      <polygon points="0,112 220,166 220,172 0,118" fill="var(--black)"/>
    </svg>
    <h2 class="serif-head abs" style="left:9px;top:171px">Who Are We?</h2>
    <p class="body-copy abs" style="left:9px;top:193px;width:201px">We are a small, highly professional and qualified group of professionals with backgrounds in law, financial services and translation and interpretation that boasts experience in global consulting and auditing firms, law firms and companies from a cross section of industries. Sensitive to the workings of the financial world, we are detail-oriented experts striving to facilitate understanding among investors, companies and international organisations.</p>
    <h2 class="serif-head abs" style="left:9px;top:289px">What We Do?</h2>
    <p class="body-copy abs" style="left:9px;top:311px;width:201px">We provide high-quality translation services in English, Spanish and French for legal and financial documents, particularly for your company's financial statements and annual reports. The translation tools we have fashioned over the years ensure that your investors and other parties recognise your company's worth and dedication while reflecting the distinction between financial statements prepared under IFRSs or local GAAP. We foster long-term relationships with our clients to develop a consistent image across varied translations and follow strict standards to maintain that consistency over time.</p>
    <svg class="abs" style="left:0;top:420px" width="220" height="84" viewBox="0 0 220 84">
      <polygon points="0,84 0,78 220,20 220,84" fill="var(--black)"/>
    </svg>
  </div>

  <div class="panel p2">
    <svg class="abs" style="left:0;top:0" width="215" height="504" viewBox="0 0 215 504" role="img" aria-label="Faint architectural photo texture">
      <polygon points="0,0 215,0 215,330 0,440" fill="#1a1a1a"/>
      <polygon points="0,440 215,330 215,334 0,446" fill="#3a3a3a"/>
    </svg>
    <div class="why-title">Why Choose Us?</div>
    <div class="benefit" style="top:62px">
      <svg width="20" height="18" viewBox="0 0 20 18"><ellipse cx="10" cy="10" rx="8" ry="6" fill="#fff"/><rect x="5" y="14" width="3" height="4" fill="#fff"/><rect x="12" y="14" width="3" height="4" fill="#fff"/><circle cx="10" cy="3" r="2" fill="#fff"/></svg>Save money</div>
    <div class="benefit" style="top:110px">
      <svg width="20" height="19" viewBox="0 0 20 19"><polygon points="10,0 12.6,6.4 19.5,6.9 14.2,11.3 15.9,18 10,14.3 4.1,18 5.8,11.3 0.5,6.9 7.4,6.4" fill="#fff"/></svg>Quality Guaranteed</div>
    <div class="benefit" style="top:158px">
      <svg width="22" height="20" viewBox="0 0 22 20"><circle cx="7" cy="8" r="3.5" fill="#fff"/><path d="M0 20c0-5 3-7 7-7s7 2 7 7z" fill="#fff"/><rect x="12" y="0" width="10" height="7" rx="2" fill="none" stroke="#fff" stroke-width="1.4"/></svg>Native Translators Only</div>
    <div class="benefit" style="top:206px">
      <svg width="20" height="20" viewBox="0 0 20 20"><circle cx="10" cy="10" r="8" fill="none" stroke="#fff" stroke-width="2"/><path d="M10 5v5h4" fill="none" stroke="#fff" stroke-width="2"/></svg>Consistency Over Time<br>(develop the customer's own voice in another language)</div>
    <div class="benefit" style="top:264px">
      <svg width="20" height="18" viewBox="0 0 20 18"><rect x="3" y="1" width="14" height="11" fill="none" stroke="#fff" stroke-width="1.8"/><rect x="0" y="14" width="20" height="3" fill="#fff"/></svg>Use of Technology Helps Cut Costs</div>
    <div class="contact" style="top:414px">120 Harbor Lane Westbrook, FL 30000<br>(555) 014-2290<br>info@lumarinservices-example.com<br>www.lumarinservices-example.com</div>
  </div>

  <div class="panel p3">
    <svg class="photo" style="left:0;top:0" width="219" height="504" viewBox="0 0 219 504" role="img" aria-label="Photo of a hand signing a document beside a justice statue">
      <defs><linearGradient id="g2" x1="0" y1="0" x2="1" y2="1"><stop offset="0" stop-color="#e2e2e2"/><stop offset=".55" stop-color="#9a9a9a"/><stop offset="1" stop-color="#2a2a2a"/></linearGradient></defs>
      <polygon points="0,80 219,64 219,250 0,330" fill="url(#g2)"/>
      <polygon points="0,72 219,52 219,64 0,80" fill="var(--black)"/>
      <polygon points="0,330 219,250 219,504 0,504" fill="var(--black)"/>
    </svg>
    <div class="brand">LUMARIN SERVICES</div>
    <div class="tagline">High-quality translation services<br>in English, Spanish and French<br>for legal and financial documents</div>
    <div class="weburl">www.lumarinservices-example.com</div>
  </div>
</div>

<div class="section-label" style="top:619px">BROCHURE INSIDE</div>

<div class="sheet sheet-inside">
  <div class="panel p1">
    <div class="expertise-title">Areas of Expertise</div>
    <div class="expertise-item" style="top:59px"><div class="num">1</div><h3>Duis autem vel eum iriure dolor</h3>
      <p class="body-copy">Lorem ipsum dolor sit amet, consectetuer adipiscing elit, sed diam nonummy nibh euismod tincidunt ut laoreet dolore magna aliquam erat volutpat. Ut wisi enim ad minim veniam, quis nostrud exerci tation ullamcorper suscipit lobortis nisl ut aliquip ex ea commodo consequat.</p></div>
    <div class="expertise-item" style="top:148px"><div class="num">2</div><h3>Duis autem vel eum iriure dolor</h3>
      <p class="body-copy">Lorem ipsum dolor sit amet, consectetuer adipiscing elit, sed diam nonummy nibh euismod tincidunt ut laoreet dolore magna aliquam erat volutpat. Ut wisi enim ad minim veniam, quis nostrud exerci tation ullamcorper suscipit lobortis nisl ut aliquip ex ea commodo consequat.</p></div>
    <div class="expertise-item" style="top:238px"><div class="num">3</div><h3>Duis autem vel eum iriure dolor</h3>
      <p class="body-copy">Lorem ipsum dolor sit amet, consectetuer adipiscing elit, sed diam nonummy nibh euismod tincidunt ut laoreet dolore magna aliquam erat volutpat. Ut wisi enim ad minim veniam, quis nostrud exerci tation ullamcorper suscipit lobortis nisl ut aliquip ex ea commodo consequat.</p></div>
    <svg class="photo" style="left:0;top:300px" width="220" height="205" viewBox="0 0 220 205" role="img" aria-label="Photo of a judge's gavel resting on a book">
      <defs><linearGradient id="g3" x1="0" y1="0" x2="1" y2="1"><stop offset="0" stop-color="#d0d0d0"/><stop offset=".6" stop-color="#8c8c8c"/><stop offset="1" stop-color="#4a4a4a"/></linearGradient></defs>
      <polygon points="0,10 220,68 220,205 0,205" fill="url(#g3)"/>
      <polygon points="0,4 220,62 220,68 0,10" fill="var(--black)"/>
    </svg>
  </div>

  <div class="panel p2">
    <div class="diff-title">Differences between working with a translation agency and a translation provider</div>
    <p class="dark-copy" style="top:94px">Lorem ipsum dolor sit amet, consectetuer adipiscing elit, sed diam nonummy nibh euismod tincidunt ut laoreet dolore magna aliquam erat volutpat. Ut wisi enim ad minim veniam, quis nostrud exerci tation ullamcorper suscipit lobortis nisl ut aliquip ex ea commodo consequat.</p>
    <ul class="bullets">
      <li>Nam liber tempor cum soluta nobis</li>
      <li>Eleifend option congue nihil imperdiet doming</li>
      <li>Id quod mazim placerat facer possim assum</li>
      <li>Typi non habent claritatem insitam; est usus</li>
      <li>Legentis in iis qui facit eorum claritatem.</li>
      <li>Investigationes demonstraverunt lectores</li>
      <li>Legere me lius quod ii legunt saepius.</li>
    </ul>
    <p class="dark-copy" style="top:313px">Duis autem vel eum iriure dolor in hendrerit in vulputate velit esse molestie consequat, vel illum dolore eu feugiat nulla facilisis at vero eros et accumsan et iusto odio dignissim qui blandit praesent luptatum zzril delenit augue duis dolore te feugait nulla facilisi. Nam liber tempor cum soluta nobis eleifend option congue nihil imperdiet doming id quod mazim placerat facer possim assum.</p>
    <p class="dark-copy" style="top:390px">Typi non habent claritatem insitam; est usus legentis in iis qui facit eorum claritatem. Investigationes demonstraverunt lectores legere me lius quod ii legunt saepius. Claritas est etiam processus dynamicus, qui sequitur mutationem consuetudium lectorum. Mirum est notare quam littera gothica, quam nunc putamus parum claram, anteposuerit litterarum formas humanitatis per seacula quarta decima et quinta decima. Eodem modo typi, qui nunc nobis videntur parum clari, fiant sollemnes in futurum.</p>
  </div>

  <div class="panel p3">
    <svg class="photo" style="left:0;top:0" width="219" height="200" viewBox="0 0 219 200" role="img" aria-label="Photo of a hand writing with a pen on a document">
      <defs><linearGradient id="g4" x1="0" y1="0" x2="1" y2="1"><stop offset="0" stop-color="#f0f0f0"/><stop offset=".6" stop-color="#b5b5b5"/><stop offset="1" stop-color="#6a6a6a"/></linearGradient></defs>
      <polygon points="0,0 219,0 219,190 0,134" fill="url(#g4)"/>
      <polygon points="0,134 219,190 219,196 0,140" fill="var(--black)"/>
    </svg>
    <div class="pricing-title">Pricing</div>
    <table class="price-table">
      <tr><th>Description</th><th class="amt">Amount</th></tr>
      <tr><td>Lorem ipsum dolor sit amet</td><td class="amt">$100</td></tr>
      <tr><td>Consectetuer adipiscing elit</td><td class="amt">$100</td></tr>
      <tr><td>Sed diam nonummy nibh</td><td class="amt">$100</td></tr>
      <tr><td>Euismod tincidunt ut laoreet dolore</td><td class="amt">$100</td></tr>
      <tr><td>Magna aliquam erat volutpat</td><td class="amt">$100</td></tr>
      <tr><td>Ut wisi enim ad minim veniam</td><td class="amt">$100</td></tr>
      <tr><td>Quis nostrud exerci tation</td><td class="amt">$100</td></tr>
      <tr><td>Ullamcorper suscipit lobortis</td><td class="amt">$100</td></tr>
      <tr><td>Nisl ut aliquip ex ea</td><td class="amt">$100</td></tr>
      <tr><td>Commodo consequat.</td><td class="amt">$100</td></tr>
    </table>
  </div>
</div>

</body>
</html>
```